Creative Law Firm Business Card

attached are photos of myself and our office as well as language that I would like to see on the card, likely on the back, although I leave that to the designer. I have also attached copies of both sides of a marketing card that we produced just for ideas. I would like to find a tactful way to get my photo in along with the office. I attached copies of our logo, both normal and inverted.

I listed my name as Tom Halloway to be casual, however, it should probably read Thomas J Halloway

Requirements
Must have
• attached file #8 has content.
• I would like my picture and the office photo on page 1
• The text, with the exception of the firm name "HALLOWAY & PEMBER" and the firm description underneath it "THE BUSINESS AND BANKRUPTCY LAWYERS", should be on the back. The layout and fonts are up to the designer

```html
<!DOCTYPE html>
<html lang="en">
<head>
<meta charset="utf-8">
<title>Halloway &amp; Pember – Business Card</title>
<link href="https://fonts.googleapis.com/css2?family=Cinzel:wght@400;600&family=Crimson+Text:wght@400;600&display=swap" rel="stylesheet">
<style>
  :root{
    --bg:#e4e4e4;
    --navy:#1c2f5e;
    --navy-deep:#15244a;
    --sky-blue:#5f95cc;
    --teal:#1b8aa0;
    --ink:#22335c;
    --paper:#ffffff;
    --rule:#2a3b66;
  }
  *{box-sizing:border-box;margin:0;padding:0}
  html,body{width:1200px;height:852px;overflow:hidden;background:var(--bg)}
  .stage{position:relative;width:1200px;height:852px;display:flex;align-items:center;justify-content:center;gap:40px}
  .card{position:relative;width:560px;height:320px;border-radius:18px;overflow:hidden;box-shadow:0 6px 18px rgba(0,0,0,.25)}

  /* front */
  .card-front__photo{position:absolute;inset:0;
    background:linear-gradient(160deg,#2f63c4 0%,#4a85d6 35%,#c9bba6 55%,#8a7a68 75%,#2a2a2a 100%)}
  .card-front__portrait{position:absolute;left:0;bottom:0;width:46%;height:78%;
    background:linear-gradient(180deg,#b99a84 0%,#9b7c68 40%,#262626 62%,#151515 100%)}
  .card-front__band{position:absolute;left:46%;right:0;top:40%;height:26%;
    background:linear-gradient(90deg,rgba(27,138,160,.85),rgba(28,47,94,.8));
    display:flex;flex-direction:column;justify-content:center;padding-left:22px;color:#fff}
  .card-front__firm{font-family:'Cinzel',serif;font-weight:400;font-size:30px;letter-spacing:1px;line-height:1}
  .card-front__tagline{font-family:'Cinzel',serif;font-size:11.5px;letter-spacing:.6px;margin-top:6px}

  /* back */
  .card-back{background:var(--paper);color:var(--ink)}
  .card-back__stripe{position:absolute;left:0;top:0;bottom:0;width:46px;background:var(--navy);border-right:5px solid var(--sky-blue)}
  .card-back__body{position:absolute;left:66px;right:22px;top:20px;bottom:16px}
  .card-back__rule{height:1px;background:var(--rule)}
  .card-back__header{display:flex;align-items:center;gap:14px;padding:8px 0}
  .card-back__mark{width:40px;height:34px;background:var(--navy);flex:none}
  .card-back__firm{font-family:'Cinzel',serif;font-weight:600;font-size:30px;color:var(--navy);letter-spacing:1px}
  .card-back__name{font-family:'Cinzel',serif;font-size:15px;margin-top:8px;letter-spacing:.5px}
  .card-back__role{font-family:'Crimson Text',serif;font-weight:600;font-size:12px;margin-bottom:6px}
  .card-back__contact{font-family:'Crimson Text',serif;font-size:12.5px;line-height:1.45;margin-top:6px;list-style:none}
  .card-back__contact li{display:flex;align-items:center;gap:6px}
  .card-back__contact svg{width:10px;height:10px;fill:var(--ink)}
  .card-back__contact .no-icon{padding-left:16px}
  .card-back__claims{font-family:'Crimson Text',serif;font-size:11px;line-height:1.35;margin-top:6px}
  .card-back__claims-head{display:flex;align-items:center;gap:8px;font-size:11.5px}
  .card-back__claims-head span{flex:1;height:1px;background:var(--rule)}
  .card-back__claims ul{list-style:none;display:grid;grid-template-columns:auto auto;column-gap:8px}
</style>
</head>
<body>
<main class="stage">
  <section class="card card-front" aria-label="Card front">
    <div class="card-front__photo" role="img" aria-label="Photo of the office building with palm trees under a blue sky"></div>
    <div class="card-front__portrait" role="img" aria-label="Portrait photo of Thomas J Halloway in a dark suit"></div>
    <div class="card-front__band">
      <div class="card-front__firm">HALLOWAY &amp; PEMBER</div>
      <div class="card-front__tagline">THE BUSINESS &amp; BANKRUPTCY LAWYERS</div>
    </div>
  </section>

  <section class="card card-back" aria-label="Card back">
    <div class="card-back__stripe"></div>
    <div class="card-back__body">
      <div class="card-back__rule"></div>
      <div class="card-back__header">
        <div class="card-back__mark"></div>
        <div class="card-back__firm">HALLOWAY &amp; PEMBER</div>
      </div>
      <div class="card-back__rule"></div>
      <div class="card-back__name">THOMAS J HALLOWAY</div>
      <div class="card-back__role">Bankruptcy Specialist – Court Mediator</div>
      <div class="card-back__rule"></div>
      <ul class="card-back__contact">
        <li class="no-icon">1280 Harbor View Rd Irvine CA 92618</li>
        <li><svg viewBox="0 0 10 10"><path d="M2 0l2 2-1 1.5c.6 1.3 1.4 2.1 2.5 2.5L7 5l2 2-1.2 2C4 9 1 6 1 1.2z"/></svg>949-555-0142</li>
        <li><svg viewBox="0 0 10 10"><path d="M0 2h10v6H0z M0 2l5 3.5L10 2" fill="none" stroke="#22335c" stroke-width="1"/></svg>tom@hallowaypember.com</li>
        <li><svg viewBox="0 0 10 10"><circle cx="5" cy="5" r="4.3" fill="none" stroke="#22335c" stroke-width="1"/><path d="M.7 5h8.6M5 .7c-2 2.4-2 6.2 0 8.6M5 .7c2 2.4 2 6.2 0 8.6" fill="none" stroke="#22335c" stroke-width=".8"/></svg>www.hallowaypember.com</li>
      </ul>
      <div class="card-back__claims">
        <div class="card-back__claims-head">36 YEARS EXPERIENCE AV RATED <span></span></div>
        <ul>
          <li>» We find an exit strategy before we act</li><li>» Practice since 1979 av rated</li>
          <li>» General counsel for your business compressive</li><li>» Business &amp; litigation services</li>
          <li>» A century of collective experience</li><li>» Bankruptcy and Reorganizations Collections</li>
        </ul>
      </div>
    </div>
  </section>
</main>
</body>
</html>
```